New Innovative Counselling and psychotherapy Service needs Business Card design

Keep it simple and professional. On one side, just company name and logo (perhaps in all blue) and maybe a tag line.

On other side (all white) my name and Qualifications in centre

Industry/Entity Type

Health And Wellness

Contact Information for Business Card

Dara Whelby
Counsellor & Psychotherapist
BSc (Psychol.), BA, Dip. (Couns. & Psych.), PG.Cert (CBT), FGTrK, ONRE

I will also require Mobile no, Email and web site address of which I'll pass on to final designer.

Font styles to use
Sans Serif

Requirements
Must have
• My Logo Only and please use the colours in logo that is in it.
Should not have
• Any other images

```html
<!DOCTYPE html>
<html lang="en">
<head>
<meta charset="utf-8">
<title>Willow Path – Business Card</title>
<link rel="stylesheet" href="https://fonts.googleapis.com/css2?family=Raleway:wght@400&family=Roboto:wght@400&family=Roboto+Condensed:wght@400;700&display=swap">
<style>
  :root {
    --stage: #3a3a3c;
    --card-white: #f4f4f4;
    --brand-blue: #46b2ec;
    --brand-green: #94d35a;
    --ink: #3d3d3d;
    --divider: #cfcfcf;
    --white: #ffffff;
  }
  * { margin: 0; padding: 0; box-sizing: border-box; }
  html, body { width: 1200px; height: 960px; overflow: hidden; }
  body { background: var(--stage); position: relative; font-family: "Roboto", Arial, sans-serif; }

  .card { position: absolute; width: 600px; height: 342px; box-shadow: 0 3px 8px rgba(0,0,0,.45); overflow: hidden; }

  /* Front */
  .card-front { left: 322px; top: 110px; background: var(--card-white); }
  .brand { position: absolute; left: 38px; top: 145px; display: flex; align-items: center; gap: 14px; }
  .brand-dot { width: 46px; height: 46px; border-radius: 50%; background: var(--brand-blue); }
  .brand-name { font-family: "Raleway", Arial, sans-serif; font-weight: 400; font-size: 26px; color: var(--ink); letter-spacing: .2px; }
  .divider { position: absolute; left: 301px; top: 95px; width: 1px; height: 155px; background: var(--divider); }
  .details { position: absolute; left: 324px; top: 96px; }
  .person-name { font-family: "Roboto Condensed", Arial, sans-serif; font-weight: 700; font-size: 21px; color: var(--brand-blue); line-height: 24px; }
  .person-role { font-family: "Roboto Condensed", Arial, sans-serif; font-weight: 700; font-size: 15px; color: var(--brand-green); line-height: 18px; }
  .person-quals { font-family: "Roboto Condensed", Arial, sans-serif; font-size: 11.5px; color: var(--brand-green); line-height: 14px; margin-top: 2px; }
  .contact { list-style: none; margin-top: 24px; }
  .contact li { display: flex; align-items: center; gap: 8px; font-size: 14.5px; color: var(--ink); line-height: 19px; }
  .contact svg { width: 14px; height: 14px; flex: none; }
  .card-band { position: absolute; left: 0; bottom: 0; width: 600px; height: 16px; }

  /* Back */
  .card-back { left: 320px; top: 493px; background: var(--brand-blue); }
  .back-mark { position: absolute; left: 0; right: 0; top: 120px; display: flex; align-items: center; justify-content: center; gap: 14px; }
  .back-mark .brand-dot { width: 40px; height: 40px; background: var(--white); }
  .back-mark .brand-name { color: var(--white); font-size: 34px; }
  .tagline { position: absolute; left: 0; right: 0; top: 288px; text-align: center; font-size: 14px; color: var(--white); }
</style>
</head>
<body>
  <section class="card card-front">
    <div class="brand">
      <span class="brand-dot"></span>
      <span class="brand-name">Willow Path</span>
    </div>
    <div class="divider"></div>
    <div class="details">
      <h1 class="person-name">DARA WHELBY</h1>
      <p class="person-role">COUNSELLOR &amp; PSYCHOTHERAPIST</p>
      <p class="person-quals">BSc (Psychol.), BA, Dip. (Couns. &amp; Psych.)<br>PG.Cert (CBT), FGTrK,</p>
      <ul class="contact">
        <li>
          <svg viewBox="0 0 14 14" aria-hidden="true"><rect x="3" y="0.5" width="8" height="13" rx="1.5" fill="none" stroke="var(--brand-blue)" stroke-width="1.6"/><circle cx="7" cy="11" r="0.9" fill="var(--brand-blue)"/></svg>
          555 210 4478
        </li>
        <li>
          <svg viewBox="0 0 14 14" aria-hidden="true"><rect x="1" y="3" width="12" height="8" fill="var(--brand-blue)"/><path d="M1 3 L7 8 L13 3" fill="none" stroke="var(--white)" stroke-width="1"/></svg>
          dara@Willowpath.com
        </li>
        <li>
          <svg viewBox="0 0 14 14" aria-hidden="true"><circle cx="7" cy="7" r="6" fill="var(--brand-blue)"/><path d="M4 4.5 Q6 5 5.5 7 Q7 8 6 10.5 M9 3.5 Q8.5 5.5 10.5 6.5" fill="none" stroke="var(--white)" stroke-width="1"/></svg>
          www.Willowpath.com
        </li>
      </ul>
    </div>
    <svg class="card-band" viewBox="0 0 600 16" aria-hidden="true">
      <polygon points="0,0 368,0 364,16 0,16" fill="var(--brand-blue)"/>
      <polygon points="372,0 600,0 600,16 368,16" fill="var(--brand-green)"/>
    </svg>
  </section>

  <section class="card card-back">
    <div class="back-mark">
      <span class="brand-dot"></span>
      <span class="brand-name">Willow Path</span>
    </div>
    <p class="tagline">Caring For Your Psychological Well-Being Is Our Top Priority</p>
  </section>
</body>
</html>
```